indépendant en tant que Massothérapeute et Préparateur Mental, j'ai besoin de ...

Massothérapeute et préparateur mental indépendant, je recherche une carte de visite sobre et dynamique, sans images liées au massage ou à la préparation mentale mais intégrant mon logo. Les couleurs que j'aime bien sont : Blanc, gris, anthracite, noir et jaune

Contact Information for Business Card

carte de préférence Horizontale
neutre qui puisse toucher le deux domaines Massothérapie et préparation mentale

Requirements
Must have
• mon projet doit intégrer au recto:
LOGO
Loïc Bardèze
078 513 26 48
info@loicbardeze.ch
et éventuellement www.loicbardeze.ch

et au verso les deux adresses:

Chemin des Ormilles 7B
1432 Valmorin-le-Lac

Route de la Gravière 9
1700 Fribourg

Should not have
• mon projet ne doit pas contenir d'image en liens avec le massage ni la préparation mentale.

```html
<!DOCTYPE html>
<html lang="fr">
<head>
<meta charset="utf-8">
<title>Loïc Bardèze – Carte de visite</title>
<link rel="stylesheet" href="https://fonts.googleapis.com/css2?family=Montserrat:wght@300;400;600;800&display=swap">
<style>
  :root {
    --backdrop: #d9d9d9;
    --anthracite: #4a4a4a;
    --yellow: #fbbd12;
    --white: #ffffff;
    --text-grey: #505050;
  }
  * { margin: 0; padding: 0; box-sizing: border-box; }
  html, body { width: 1200px; height: 965px; overflow: hidden; }
  body {
    background: var(--backdrop);
    font-family: "Montserrat", Arial, sans-serif;
    position: relative;
  }
  .card {
    position: absolute;
    left: 200px;
    width: 800px;
    height: 440px;
    overflow: hidden;
    box-shadow: 0 6px 18px rgba(0,0,0,.25);
  }
  .card--back { top: 28px; background: var(--anthracite); color: var(--white); }
  .card--front { top: 497px; background: var(--white); color: var(--text-grey); }

  .brand { position: absolute; display: flex; align-items: center; gap: 14px; }
  .brand__dot { width: 18px; height: 18px; border-radius: 50%; background: var(--yellow); flex: none; }
  .brand__text { display: flex; flex-direction: column; }
  .brand__name { font-weight: 800; font-size: 38px; letter-spacing: 1px; line-height: 1; }
  .brand__role { font-weight: 400; font-size: 11.5px; letter-spacing: 1.6px; text-transform: uppercase; margin-top: 6px; }

  .card--back .brand { left: 60px; top: 70px; }
  .card--front .brand { left: 60px; top: 66px; color: var(--anthracite); }

  .address { position: absolute; font-weight: 300; font-size: 24px; line-height: 1.3; }
  .address--first { left: 60px; bottom: 60px; text-align: center; }
  .address--second { left: 500px; top: 210px; text-align: center; }
  .address-pin { position: absolute; left: 420px; top: 262px; width: 34px; height: 44px; }

  .swoosh { position: absolute; inset: 0; width: 800px; height: 440px; }

  .holder { position: absolute; left: 60px; top: 200px; font-weight: 800; font-size: 26px; color: var(--yellow); letter-spacing: .5px; }

  .contact { position: absolute; left: 60px; top: 262px; list-style: none; }
  .contact__item { display: flex; align-items: center; gap: 14px; font-weight: 400; font-size: 22px; line-height: 1.45; color: var(--text-grey); }
  .contact__icon { width: 20px; height: 20px; flex: none; }
</style>
</head>
<body>

  <section class="card card--back">
    <div class="brand">
      <span class="brand__dot"></span>
      <div class="brand__text">
        <span class="brand__name">Loïc Bardèze</span>
        <span class="brand__role">Massothérapeute / Préparateur mental</span>
      </div>
    </div>

    <p class="address address--first">Chemin des Ormilles 7B<br>1432 Valmorin-le-Lac</p>

    <svg class="address-pin" viewBox="0 0 34 44" aria-hidden="true">
      <path d="M17 42 C8 30 3 23 3 16 A14 14 0 0 1 31 16 C31 23 26 30 17 42 Z" fill="none" stroke="var(--yellow)" stroke-width="2.5"/>
      <circle cx="17" cy="16" r="5.5" fill="none" stroke="var(--yellow)" stroke-width="2.5"/>
    </svg>

    <p class="address address--second">Route de la Gravière 9<br>1726 Corbeval</p>
  </section>

  <section class="card card--front">
    <svg class="swoosh" viewBox="0 0 800 440" aria-hidden="true">
      <path d="M500 0 H800 V240 C775 110 660 25 500 0 Z" fill="var(--yellow)"/>
      <path d="M800 120 C795 290 700 385 580 440 H800 Z" fill="var(--anthracite)"/>
      <path d="M800 280 C790 350 765 400 730 440 H800 Z" fill="var(--white)"/>
      <path d="M800 300 C792 360 770 405 742 440 H800 Z" fill="var(--yellow)"/>
    </svg>

    <div class="brand">
      <span class="brand__dot"></span>
      <div class="brand__text">
        <span class="brand__name">Loïc Bardèze</span>
        <span class="brand__role">Massothérapeute / Préparateur mental</span>
      </div>
    </div>

    <p class="holder">Loïc Bardèze</p>

    <ul class="contact">
      <li class="contact__item">
        <svg class="contact__icon" viewBox="0 0 20 20" aria-hidden="true"><path d="M5 2 L8 6 L6 8 C7 11 9 13 12 14 L14 12 L18 15 L16 18 C9 18 2 11 2 4 Z" fill="none" stroke="var(--yellow)" stroke-width="1.6" stroke-linejoin="round"/></svg>
        078 513 26 48
      </li>
      <li class="contact__item">
        <svg class="contact__icon" viewBox="0 0 20 20" aria-hidden="true"><rect x="2" y="4" width="16" height="12" fill="none" stroke="var(--yellow)" stroke-width="1.6"/><path d="M2 4 L10 11 L18 4" fill="none" stroke="var(--yellow)" stroke-width="1.6"/></svg>
        info@loicbardeze.ch
      </li>
      <li class="contact__item">
        <svg class="contact__icon" viewBox="0 0 20 20" aria-hidden="true"><circle cx="10" cy="10" r="8" fill="none" stroke="var(--yellow)" stroke-width="1.6"/><ellipse cx="10" cy="10" rx="3.5" ry="8" fill="none" stroke="var(--yellow)" stroke-width="1.4"/><path d="M2 10 H18 M3.5 6 H16.5 M3.5 14 H16.5" stroke="var(--yellow)" stroke-width="1.4"/></svg>
        www.loicbardeze.ch
      </li>
    </ul>
  </section>

</body>
</html>
```